Online Shop - Website Design for up an coming art studio

We require a fully functional website design - not just design - but complete coded online shop website please, which should be a word press style frame work to allow ease up updating the site in the future. The website will sell art work from up and coming artists. The business is called "Brindle Harbor Studios". I have attached our logo to allow the submitted designs to tie in with this.

Industry/Entity Type

Shop

Coding

Coded - Design and coding required

Number of Pages Required

1 page

Colors

Designer to choose colors to be used in the design.

Requirements
Must have
• The website design must incorporate and fully functional online eCommerce shop feature.

```html
<!DOCTYPE html>
<html lang="en">
<head>
<meta charset="utf-8">
<title>Brindle Harbor Studios</title>
<link rel="stylesheet" href="https://fonts.googleapis.com/css2?family=Montserrat:wght@400;600;700&family=Arimo:wght@400;700&family=Noto+Serif:ital@1&display=swap">
<style>
:root{
  --blue:#1fa3dc;
  --blue-light:#44b6ea;
  --blue-dark:#1790cc;
  --ink:#2f2f2f;
  --text:#666;
  --muted:#8a8a8a;
  --line:#e3e3e3;
  --soft:#f6f7f9;
  --olive:#b9c46d;
  --green:#6db43c;
  --footer:#474747;
}
*{margin:0;padding:0;box-sizing:border-box}
html,body{width:1200px;height:2273px;overflow:hidden;background:#fff}
body{position:relative;font-family:"Arimo",Arial,sans-serif;color:var(--text)}
.abs{position:absolute}
.rainbow{left:0;top:0;width:1200px;height:4px;background:linear-gradient(90deg,#f2c500,#e84c3d,#9b59b6,#3498db,#1abc9c,#6db43c,#f39c12)}
.contact-chip{display:flex;align-items:center;gap:20px;font:400 14px "Montserrat",sans-serif;color:#444}
.chip-icon{width:46px;height:46px;border:1.5px solid var(--olive);border-radius:50%;display:flex;align-items:center;justify-content:center;flex:none}
.phone-chip{left:86px;top:21px}
.address-chip{left:817px;top:18px;line-height:23px}
.nav{left:86px;top:89px;width:1028px;height:49px;background:linear-gradient(var(--blue-light),var(--blue-dark));border-radius:3px 3px 0 0}
.nav a{position:absolute;top:17px;color:#fff;font:600 12px "Montserrat",sans-serif;text-decoration:none;text-transform:uppercase}
.brand{left:500px;top:60px;width:182px;height:128px;background:#fff;border-radius:0 0 91px 91px;display:flex;flex-direction:column;align-items:center;justify-content:center;gap:8px;padding-top:10px;z-index:2}
.brand-dot{width:36px;height:36px;border-radius:50%;background:#3a3a3a}
.brand-name{font:600 13px "Montserrat",sans-serif;color:#555;letter-spacing:.5px;text-align:center;line-height:16px}
.hero{left:86px;top:138px;width:1028px;height:432px;background:radial-gradient(circle at 62% 55%,#f6d27a 0%,#ee9d4a 30%,#c96a4a 55%,transparent 75%),linear-gradient(160deg,#3d6f8e 0%,#8e8aa0 30%,#e39a55 60%,#8b4a3a 100%);border-radius:0 0 3px 3px}
.hero-tree{left:560px;top:160px;width:420px;height:260px;border-radius:50%;background:radial-gradient(#d8386a,#b52a5a 50%,transparent 72%);opacity:.75}
.hero-copy{left:122px;top:338px;width:320px;color:#fff}
.hero-copy h1{font:600 22px "Montserrat",sans-serif;text-transform:uppercase;margin-bottom:12px;white-space:nowrap}
.hero-copy p{font-size:12px;line-height:26px}
.btn{display:inline-block;background:var(--blue);color:#fff;font:600 12px "Montserrat",sans-serif;text-transform:uppercase;padding:9px 18px;border-radius:2px;margin-top:14px}
.dots{left:576px;top:545px;display:flex;gap:6px}
.dots span{width:13px;height:13px;border:2px solid #fff;border-radius:50%}
.dots span.on{background:var(--blue)}
.welcome-kicker{left:86px;top:609px;font:400 19px "Montserrat",sans-serif;color:#444;text-transform:uppercase}
.welcome-title{left:86px;top:639px;font:600 24px "Montserrat",sans-serif;color:var(--blue);text-transform:uppercase}
.welcome-text{left:86px;top:692px;width:512px;font-size:11.5px;line-height:26px}
.welcome-text p+p{margin-top:20px}
.video{left:653px;top:618px;width:459px;height:298px;background:linear-gradient(180deg,#c9d2d8 0%,#9aa1a0 40%,#6e6a5e 75%,#8b8a84 100%)}
.play{left:856px;top:741px;width:52px;height:52px;border-radius:50%;background:rgba(0,0,0,.45);border:2px solid #fff}
.featured{left:0;top:967px;width:1200px;height:510px;background:var(--soft)}
.section-title{left:0;width:1200px;text-align:center;font:600 19px "Montserrat",sans-serif;color:var(--blue);text-transform:uppercase}
.section-lead{left:0;width:1200px;text-align:center;font-size:11.5px}
.card{top:1082px;width:247px;height:357px;background:#fff;border:1px solid #e8e8e8}
.card-art{position:absolute;left:7px;top:7px;width:231px;height:209px}
.price{position:absolute;left:0;top:230px;width:100%;text-align:center;font:700 20px "Montserrat",sans-serif;color:var(--blue)}
.card-name{position:absolute;left:0;top:264px;width:100%;text-align:center;font:600 14px "Montserrat",sans-serif;color:#444;text-transform:uppercase}
.actions{position:absolute;left:0;top:297px;width:100%;display:flex;justify-content:center;gap:8px}
.actions span{width:34px;height:34px;border:1px solid #ddd;border-radius:50%;display:flex;align-items:center;justify-content:center}
.actions span.on{background:var(--blue);border-color:var(--blue)}
.artist{top:1583px;width:329px}
.artist-art{height:197px}
.artist h3{margin-top:26px;font:600 16px "Montserrat",sans-serif;color:var(--ink);text-transform:uppercase}
.artist p{margin-top:14px;font-size:11.5px;line-height:23px}
.meta{margin-top:12px;display:flex;align-items:center;gap:8px;font:italic 12px "Noto Serif",serif;color:var(--blue)}
.footer{left:0;top:1947px;width:1200px;height:259px;background:var(--soft)}
.map{left:86px;top:1997px;width:253px;height:170px;background:linear-gradient(135deg,#eef0e6,#dfe3d6 60%,#f0d9a6)}
.foot-title{top:1992px;font:600 15px "Montserrat",sans-serif;color:#444;text-transform:uppercase}
.foot-list{left:394px;top:2035px;font-size:11.5px;line-height:15px}
.foot-list li{list-style:none;display:flex;gap:14px;margin-bottom:15px}
.foot-list u{color:#666}
.news-text{left:661px;top:2034px;width:240px;font-size:11.5px;line-height:21px}
.email-field{left:661px;top:2091px;width:214px;height:34px;border:1px solid #ccc;background:#fff;font-size:11.5px;color:#444;padding:9px 14px}
.subscribe{left:661px;top:2133px;background:var(--green);color:#fff;font:700 10px "Montserrat",sans-serif;padding:7px 11px;text-transform:uppercase}
.follow-text{left:908px;top:2037px;width:220px;font-size:11.5px;line-height:19px;color:var(--muted)}
.socials{left:906px;top:2112px;display:flex;gap:9px}
.socials span{width:35px;height:35px;border:1.5px solid #bbb;border-radius:50%}
.copyright{left:0;top:2206px;width:1200px;height:67px;background:var(--footer);color:#fff;font-size:11.5px;text-align:center;line-height:67px}
</style>
</head>
<body>
<div class="abs rainbow"></div>

<div class="abs contact-chip phone-chip">
  <span class="chip-icon"><svg width="14" height="14" viewBox="0 0 24 24"><path fill="#b9c46d" d="M6.6 10.8a15 15 0 0 0 6.6 6.6l2.2-2.2c.3-.3.7-.4 1-.2 1.1.4 2.3.6 3.6.6.6 0 1 .4 1 1V20c0 .6-.4 1-1 1A17 17 0 0 1 3 4c0-.6.4-1 1-1h3.5c.6 0 1 .4 1 1 0 1.3.2 2.5.6 3.6.1.3 0 .7-.2 1z"/></svg></span>
  <span>Call Us : (000)-555-0148</span>
</div>
<div class="abs contact-chip address-chip">
  <span class="chip-icon"><svg width="12" height="16" viewBox="0 0 12 16"><path fill="#b9c46d" d="M6 0a6 6 0 0 0-6 6c0 4.5 6 10 6 10s6-5.5 6-10a6 6 0 0 0-6-6zm0 8.5A2.5 2.5 0 1 1 6 3.5a2.5 2.5 0 0 1 0 5z"/></svg></span>
  <span>42 Larkspur Lane, Millbrook,<br>Eastshire, Scotland, EX4 7QT</span>
</div>

<nav class="abs nav">
  <a style="left:36px">Home</a>
  <a style="left:146px">About Us</a>
  <a style="left:282px">Services</a>
  <a style="left:643px">Products</a>
  <a style="left:783px">Gallery</a>
  <a style="left:911px">Contact Us</a>
</nav>

<div class="abs hero" role="img" aria-label="Painted sunset landscape with a blossoming red tree and a lone traveller"></div>
<div class="abs hero-tree" aria-hidden="true"></div>
<div class="abs hero-copy">
  <h1>Brindle Harbor Studios</h1>
  <p>Sed ut perspiciatis unde omnis iste natus error sit volupt tatem accusantium doloremque laudantium, totam rem architecto beatae vitae dicta sunt explicabo.</p>
  <span class="btn">Read More</span>
</div>
<div class="abs dots"><span></span><span class="on"></span><span></span></div>

<div class="abs brand">
  <span class="brand-dot"></span>
  <span class="brand-name">BRINDLE HARBOR<br>STUDIOS</span>
</div>

<div class="abs welcome-kicker">Welcome to</div>
<div class="abs welcome-title">Brindle Harbor Studios</div>
<div class="abs welcome-text">
  <p>Sed ut perspiciatis unde omnis iste natus error sit voluptatem accusantium doloremque laudantium, totam rem aperiam, eaque ipsa quae ab illo inventore veritatis et quasi architecto beatae vitae dicta sunt explicabo. Nemo enim ipsam voluptatem quia voluptas sit aspernaturma gni dolores eos qui ratione voluptatem sequi nesciunt.</p>
  <p>Sed ut perspiciatis unde omnis iste natus error sit voluptatem accusantium doloremque laudantium, totam rem aperiam, eaque ipsa quae ab illo inventore veritatis et quasi architecto beatae voluptatem quia voluptas sit atae vitae dicta sunt explicabo.</p>
</div>
<div class="abs video" role="img" aria-label="Video preview: painted city street with yellow taxis"></div>
<div class="abs play"><svg width="48" height="48"><path d="M19 14l15 10-15 10z" fill="#fff"/></svg></div>

<section class="abs featured"></section>
<h2 class="abs section-title" style="top:1002px">Featured Products</h2>
<p class="abs section-lead" style="top:1041px">Sed ut perspiciatis unde omnis iste natus error sit voluptatem accusantium doloremque laudantium, totam</p>

<div class="abs card" style="left:86px">
  <div class="card-art" role="img" aria-label="Painting of red poppies on a cream background" style="background:linear-gradient(160deg,#e8d9bf,#b56a45 60%,#7a3d28)"></div>
  <div class="price">$ 89,00</div><div class="card-name">Contrary to popular</div>
  <div class="actions"><span class="on"><svg width="14" height="14" viewBox="0 0 24 24"><path fill="#fff" d="M7 18a2 2 0 1 0 0 4 2 2 0 0 0 0-4zm10 0a2 2 0 1 0 0 4 2 2 0 0 0 0-4zM1 2v2h2l3.6 7.6L5.2 14c-.1.3-.2.6-.2 1 0 1.1.9 2 2 2h12v-2H7.4l1.1-2h7.5c.8 0 1.4-.4 1.7-1l3.6-6.5L19.6 4H5.2l-.9-2z"/></svg></span><span><svg width="13" height="12" viewBox="0 0 24 22"><path fill="none" stroke="#aaa" stroke-width="2" d="M12 20S2 13.5 2 7a5 5 0 0 1 10-1 5 5 0 0 1 10 1c0 6.5-10 13-10 13z"/></svg></span><span><svg width="13" height="12" viewBox="0 0 14 12"><path d="M1 3h11M9 0l3 3-3 3M13 9H2M5 6 2 9l3 3" fill="none" stroke="#e07a3d" stroke-width="1.4"/></svg></span></div>
</div>
<div class="abs card" style="left:346px">
  <div class="card-art" role="img" aria-label="Artwork of a brain half grey, half bursting with colour" style="background:linear-gradient(90deg,#cfc8bf,#b8b0a6 48%,#e5553a 52%,#c43a7a 75%,#4a6fd0)"></div>
  <div class="price">$ 89,00</div><div class="card-name">Contrary to popular</div>
  <div class="actions"><span><svg width="14" height="14" viewBox="0 0 24 24"><path fill="#aaa" d="M7 18a2 2 0 1 0 0 4 2 2 0 0 0 0-4zm10 0a2 2 0 1 0 0 4 2 2 0 0 0 0-4zM1 2v2h2l3.6 7.6L5.2 14c-.1.3-.2.6-.2 1 0 1.1.9 2 2 2h12v-2H7.4l1.1-2h7.5c.8 0 1.4-.4 1.7-1l3.6-6.5L19.6 4H5.2l-.9-2z"/></svg></span><span><svg width="13" height="12" viewBox="0 0 24 22"><path fill="none" stroke="#aaa" stroke-width="2" d="M12 20S2 13.5 2 7a5 5 0 0 1 10-1 5 5 0 0 1 10 1c0 6.5-10 13-10 13z"/></svg></span><span><svg width="13" height="12" viewBox="0 0 14 12"><path d="M1 3h11M9 0l3 3-3 3M13 9H2M5 6 2 9l3 3" fill="none" stroke="#aaa" stroke-width="1.4"/></svg></span></div>
</div>
<div class="abs card" style="left:606px">
  <div class="card-art" role="img" aria-label="Sepia painting of a city street with a red umbrella" style="background:linear-gradient(180deg,#d8d0b4,#a89a72 55%,#5e553c)"></div>
  <div class="price">$ 89,00</div><div class="card-name">Contrary to popular</div>
  <div class="actions"><span><svg width="14" height="14" viewBox="0 0 24 24"><path fill="#aaa" d="M7 18a2 2 0 1 0 0 4 2 2 0 0 0 0-4zm10 0a2 2 0 1 0 0 4 2 2 0 0 0 0-4zM1 2v2h2l3.6 7.6L5.2 14c-.1.3-.2.6-.2 1 0 1.1.9 2 2 2h12v-2H7.4l1.1-2h7.5c.8 0 1.4-.4 1.7-1l3.6-6.5L19.6 4H5.2l-.9-2z"/></svg></span><span><svg width="13" height="12" viewBox="0 0 24 22"><path fill="none" stroke="#aaa" stroke-width="2" d="M12 20S2 13.5 2 7a5 5 0 0 1 10-1 5 5 0 0 1 10 1c0 6.5-10 13-10 13z"/></svg></span><span><svg width="13" height="12" viewBox="0 0 14 12"><path d="M1 3h11M9 0l3 3-3 3M13 9H2M5 6 2 9l3 3" fill="none" stroke="#aaa" stroke-width="1.4"/></svg></span></div>
</div>
<div class="abs card" style="left:866px">
  <div class="card-art" role="img" aria-label="Painting of a white bicycle carrying purple flowers" style="background:linear-gradient(160deg,#7fa06a,#b59ad0 40%,#e8e6ee 70%,#c9c4cf)"></div>
  <div class="price">$ 89,00</div><div class="card-name">Contrary to popular</div>
  <div class="actions"><span><svg width="14" height="14" viewBox="0 0 24 24"><path fill="#aaa" d="M7 18a2 2 0 1 0 0 4 2 2 0 0 0 0-4zm10 0a2 2 0 1 0 0 4 2 2 0 0 0 0-4zM1 2v2h2l3.6 7.6L5.2 14c-.1.3-.2.6-.2 1 0 1.1.9 2 2 2h12v-2H7.4l1.1-2h7.5c.8 0 1.4-.4 1.7-1l3.6-6.5L19.6 4H5.2l-.9-2z"/></svg></span><span><svg width="13" height="12" viewBox="0 0 24 22"><path fill="none" stroke="#aaa" stroke-width="2" d="M12 20S2 13.5 2 7a5 5 0 0 1 10-1 5 5 0 0 1 10 1c0 6.5-10 13-10 13z"/></svg></span><span><svg width="13" height="12" viewBox="0 0 14 12"><path d="M1 3h11M9 0l3 3-3 3M13 9H2M5 6 2 9l3 3" fill="none" stroke="#aaa" stroke-width="1.4"/></svg></span></div>
</div>

<h2 class="abs section-title" style="top:1502px">Upcoming Artists</h2>
<p class="abs section-lead" style="top:1541px">Sed ut perspiciatis unde omnis iste natus error sit voluptatem accusantium doloremque laudantium, totam</p>

<article class="abs artist" style="left:86px">
  <div class="artist-art" role="img" aria-label="Painting of leaping dolphins in blue and white" style="background:linear-gradient(150deg,#1d2a3a,#8fa2b8 40%,#dfe6ee 60%,#2a3548)"></div>
  <h3>Neque porro quisquam</h3>
  <p>Sed ut perspiciatis unde omnis iste natus error sit voluptatem accusantiumue ipsa beatae vitae dicta sunt explicabo.</p>
  <div class="meta"><svg width="11" height="11"><rect x=".5" y="1.5" width="10" height="9" fill="none" stroke="#1fa3dc"/><path d="M.5 4h10" stroke="#1fa3dc"/></svg>1 month ago &nbsp;<svg width="12" height="11"><path d="M6 1C3 1 1 3 1 5s1 3 2 3.5L2.5 10 5 9h1c3 0 5-2 5-4S9 1 6 1z" fill="none" stroke="#1fa3dc"/></svg>05 Comments</div>
</article>
<article class="abs artist" style="left:436px">
  <div class="artist-art" role="img" aria-label="Fantasy painting of a glowing sky with floating lanterns" style="background:radial-gradient(circle at 50% 60%,#7fe0f0,#2a7fc9 35%,#2a2f7a 70%,#1b1d45)"></div>
  <h3>Neque porro quisquam</h3>
  <p>Sed ut perspiciatis unde omnis iste natus error sit voluptatem accusantiumue ipsa beatae vitae dicta sunt explicabo.</p>
  <div class="meta"><svg width="11" height="11"><rect x=".5" y="1.5" width="10" height="9" fill="none" stroke="#1fa3dc"/><path d="M.5 4h10" stroke="#1fa3dc"/></svg>1 month ago &nbsp;<svg width="12" height="11"><path d="M6 1C3 1 1 3 1 5s1 3 2 3.5L2.5 10 5 9h1c3 0 5-2 5-4S9 1 6 1z" fill="none" stroke="#1fa3dc"/></svg>05 Comments</div>
</article>
<article class="abs artist" style="left:785px">
  <div class="artist-art" role="img" aria-label="Abstract painting of red and orange flowers" style="background:radial-gradient(circle at 40% 50%,#e04a2a,#b5202a 40%,#3a2a35 80%)"></div>
  <h3>Neque porro quisquam</h3>
  <p>Sed ut perspiciatis unde omnis iste natus error sit voluptatem accusantiumue ipsa beatae vitae dicta sunt explicabo.</p>
  <div class="meta"><svg width="11" height="11"><rect x=".5" y="1.5" width="10" height="9" fill="none" stroke="#1fa3dc"/><path d="M.5 4h10" stroke="#1fa3dc"/></svg>1 month ago &nbsp;<svg width="12" height="11"><path d="M6 1C3 1 1 3 1 5s1 3 2 3.5L2.5 10 5 9h1c3 0 5-2 5-4S9 1 6 1z" fill="none" stroke="#1fa3dc"/></svg>05 Comments</div>
</article>

<footer class="abs footer"></footer>
<div class="abs map" role="img" aria-label="Street map showing the studio location"></div>

<h4 class="abs foot-title" style="left:394px">Contact Us</h4>
<ul class="abs foot-list">
  <li><svg width="12" height="12" viewBox="0 0 24 24"><path fill="#888" d="M6.6 10.8a15 15 0 0 0 6.6 6.6l2.2-2.2c.3-.3.7-.4 1-.2 1.1.4 2.3.6 3.6.6.6 0 1 .4 1 1V20c0 .6-.4 1-1 1A17 17 0 0 1 3 4c0-.6.4-1 1-1h3.5c.6 0 1 .4 1 1 0 1.3.2 2.5.6 3.6.1.3 0 .7-.2 1z"/></svg>(000)-555-0148 (Phone)</li>
  <li><svg width="12" height="12"><rect x="2" y="0" width="8" height="4" fill="#888"/><rect x="0" y="4" width="12" height="5" fill="#888"/><rect x="2" y="8" width="8" height="4" fill="#888"/></svg>(000)-555-0149 (Fax)</li>
  <li><svg width="12" height="10"><rect x=".5" y=".5" width="11" height="9" fill="#888"/><path d="M.5 .5l5.5 5 5.5-5" fill="none" stroke="#fff"/></svg><u>hello@brindleharbor.example</u></li>
  <li><svg width="10" height="13" viewBox="0 0 12 16"><path fill="#888" d="M6 0a6 6 0 0 0-6 6c0 4.5 6 10 6 10s6-5.5 6-10a6 6 0 0 0-6-6zm0 8.5A2.5 2.5 0 1 1 6 3.5a2.5 2.5 0 0 1 0 5z"/></svg><span>42 Larkspur Lane, Millbrook,<br>Eastshire, Scotland, EX4 7QT</span></li>
</ul>

<h4 class="abs foot-title" style="left:661px">Newsletter</h4>
<p class="abs news-text">Register Your email address to get information ablout us</p>
<div class="abs email-field">Email Address</div>
<div class="abs subscribe">Subscribe</div>

<h4 class="abs foot-title" style="left:908px">Follow Us</h4>
<p class="abs follow-text">Lorem ipsum dolor sit amet, conse ctetur adipiscing elit. Nulla in purus nibh. Donec ornare</p>
<div class="abs socials"><span></span><span></span><span></span><span></span><span></span></div>

<div class="abs copyright">© Copyright 2017 Brindle Harbor Studios.All Rights Reserved</div>
</body>
</html>
```